Etiketten-Design für Dankeswein
Zielgruppe
Kelvora:
Wir stellen für unsere Kunden einen Dankeswein her. Er soll eine Hommage an die Freundschaft und Partnerschaft sein.
Subtitle, could be, but perhaps not:
Good company, every moment counts.
Name: Kelvora (evtl. Änderung auf Tarnis)
Aufgabenstellung
Das Ettikett darf auch bunt sein, aber es sollte vorallem sehr Professionell sein.
Der Wein wird rötlich sein, die Flasche weiss durchsichtig. Es werden wahrscheinlich 0,5l Flaschen.
Die Form des Ettikets, kann noch definiert werden.
Es geht um eine Homage an das Treffen von Menschen und die Freundschaft.
Kelvora
Hintergrundinfos, die eher für den Hintergrund, Einarbeitung und kleine Abbildung gedacht sind.
PLORAX: ist eine IT Firma, die von 2 Partnern gegründet wurde. Das Logo sollte mit drauf, evtl. kann man auch sich an diesen Farben orientieren.
Familie Dormak: Die Tiersymbole repräsentieren die beiden Eltern. Das geschwungene H ist das Familienzeichen. Wenn man es rotiert. ähnelt es wieder einem Schmetterling. Vielleicht kann man da grafisch etwas machen?
Das geschwungene H oder die Tiersymbole haben hohen emotionalen Wert. In dem Wappen ist das neue Familiensymbol eingearbeitet in das noch ältere Familienwappen der Familie. Prio hat das geschwungene H
Für das Ettikett gibt es leider rechtliche Pflichtangaben:
PLORAX GmbH
Lindauring 14 CH-4057 Basel
Erzeugerab füllung:D- RP 7 348 962
A.P.-Nr.7 348 962 XXXX
11,0%vol 50 cl Enthält Sulfite
Deutscher Qualitätswein – Mosel
kelvora-beispiel.eu

```html
<!DOCTYPE html>
<html lang="de">
<head>
<meta charset="utf-8">
<title>Kelvora Rotling – Etikett</title>
<link rel="stylesheet" href="https://fonts.googleapis.com/css2?family=Roboto+Condensed:wght@300;400;700&family=Roboto:wght@400&display=swap">
<style>
  :root {
    --page: #ffffff;
    --label-cream: #fdfbe9;
    --label-edge: #e2dfca;
    --frame-grey: #9c9c9c;
    --ink-grey: #555557;
    --band-grey: #58585a;
    --band-text: #f2f2f2;
    --name-blue: #00b2e3;
    --art-light: #eeece0;
    --art-dark: #c9c7bd;
  }
  * { margin: 0; padding: 0; box-sizing: border-box; }
  html, body {
    width: 848px; height: 1200px; overflow: hidden;
    background: var(--page);
  }
  .canvas { position: relative; width: 848px; height: 1200px; }

  .label {
    position: absolute; left: 64px; top: 237px;
    width: 720px; height: 726px;
    background: var(--label-cream);
    border: 1px solid var(--label-edge);
    font-family: "Roboto Condensed", sans-serif;
    color: var(--ink-grey);
  }
  .label-frame {
    position: absolute; left: 15px; top: 12px;
    width: 688px; height: 695px;
    border: 1px solid var(--frame-grey);
  }
  .bottler-line {
    position: absolute; left: 20px; bottom: 34px;
    writing-mode: vertical-rl; transform: rotate(180deg);
    font-family: "Roboto", sans-serif;
    font-size: 16px; white-space: nowrap;
    background: var(--label-cream); padding: 4px 0;
  }
  .family-emblems {
    position: absolute; left: 124px; top: 8px;
    width: 518px; height: 210px;
    background: radial-gradient(ellipse at center, var(--art-dark) 0%, var(--art-light) 55%, var(--label-cream) 100%);
  }
  .wine-name {
    position: absolute; left: 0; right: 0; top: 268px;
    text-align: center;
    font-family: "Roboto Condensed", sans-serif; font-weight: 700;
    font-size: 104px; line-height: 1;
    color: var(--name-blue);
  }
  .tagline {
    position: absolute; left: 12px; right: 0; top: 404px;
    text-align: center;
    font-size: 27px; line-height: 32px; font-weight: 400;
  }
  .vintage-band {
    position: absolute; left: 63px; top: 481px;
    width: 596px; height: 56px;
    background: var(--band-grey);
    color: var(--band-text);
    font-family: "Roboto", sans-serif; font-size: 32px;
    display: flex; align-items: center; justify-content: center;
  }
  .wine-type {
    position: absolute; left: 0; right: 0; top: 548px;
    text-align: center;
    font-size: 28px; font-weight: 700; letter-spacing: 6px;
  }
  .volume {
    position: absolute; left: 550px; top: 574px;
    font-size: 48px; font-weight: 400;
  }
  .facts {
    position: absolute; left: 555px; top: 636px;
    font-size: 21px; line-height: 26px;
    background: var(--label-cream);
  }
  .producer-name {
    position: absolute; left: 243px; top: 638px;
    font-size: 60px; font-weight: 300; letter-spacing: 2px;
    color: var(--ink-grey);
    background: var(--label-cream); padding: 0 6px; line-height: 70px;
  }
</style>
</head>
<body>
<div class="canvas">
  <div class="label">
    <div class="label-frame"></div>
    <div class="bottler-line">Abfüllung: Herstelleradresse, Weingut, Straße Nr. 0, 0000 Stadt</div>
    <div class="family-emblems" role="img" aria-label="Illustration: Schmetterling, Fuchskopf und geschwungenes Familien-H als Linienzeichnung"></div>
    <div class="wine-name">Kelvora</div>
    <p class="tagline">GOOD COMPANY,<br>EVERY MOMENT COUNTS</p>
    <div class="vintage-band">2020</div>
    <div class="wine-type">ROTLING</div>
    <div class="volume">0,5 l</div>
    <div class="facts">13% vol.<br>enthält Sulfite</div>
    <div class="producer-name">PLORAX</div>
  </div>
</div>
</body>
</html>
```